Health Clinic treating people with mental illness needs a website

We need a website for a new mental health clinic based in Florida called Solvane Wellness USA. We treat people with mental health issues such as depression, PTSD, Bipolar, chronic pain, etc. I want the website to be easy to follow and inviting to the visitors. It should be easy to locate the different treatment options and how to go about contacting and making appointments. The images on the website should be something that the patients can relate to, whether a close up of a woman's face, something that conveys emotion. The patients visiting this website are often sad and miserable, they need to be able to feel comfortable when they look at this website. I want them to feel that we understand where they are coming from. I like colors such as purple, turquoise, lavender.

Target Market(s)

College students, veterans, anyone with mental illness

Industry/Entity Type

Health And Wellness

Font styles to use
Serif
Sans Serif

Colors

Designer to choose colors to be used in the design.

Requirements
Must have
• There should be a home/landing page, about us page, treatment page, contact page, and a FAQ page. I've included my logo below.
Nice to have
• The flow of the web pages should be calming and welcoming. I want people to feel warm and understood when they enter our page.
Should not have
• The images and writing should not be overly stimulating or aggressive.

```html
<!DOCTYPE html>
<html lang="en">
<head>
<meta charset="utf-8">
<title>Solvane Wellness USA</title>
<link href="https://fonts.googleapis.com/css2?family=Mulish:ital,wght@0,400;0,600;0,700;0,800;1,400&display=swap" rel="stylesheet">
<style>
:root{
  --purple:#8e2d8a;
  --purple-deep:#5a1f6e;
  --teal:#76c6b8;
  --teal-text:#3aa58f;
  --ink:#222;
  --line:#e3e3e3;
  --white:#fff;
}
*{box-sizing:border-box;margin:0;padding:0}
html,body{width:1200px;height:3894px;overflow:hidden;background:var(--white)}
body{position:relative;font-family:'Mulish',sans-serif;color:var(--ink)}
.abs{position:absolute}
a{color:inherit}

/* header */
.topbar{left:0;top:0;width:1200px;height:136px;border-bottom:1px solid var(--line)}
.contact-line{left:77px;top:64px;font-size:15px;color:#333}
.brand{left:0;width:1200px;top:54px;display:flex;justify-content:center;align-items:center;gap:10px;font-size:28px;font-weight:700;color:var(--purple-deep)}
.brand i{width:16px;height:16px;border-radius:50%;background:var(--purple-deep);display:block}
.socials{left:928px;top:66px;display:flex;gap:16px;align-items:center}
.socials span{width:14px;height:14px;border-radius:50%;background:#222;display:block}
.login{left:1054px;top:63px;font-size:15px;color:#333;display:flex;gap:12px;align-items:center}
.login i{width:15px;height:15px;border-radius:50%;background:#222;display:block}
.nav{left:0;top:136px;width:1200px;height:76px;border-bottom:1px solid var(--line)}
.nav ul{list-style:none;position:absolute;top:28px;left:393px;display:flex;gap:35px;font-size:15px;color:#333}
.nav li.active{color:var(--purple);font-weight:600}

/* hero */
.hero{left:0;top:212px;width:1200px;height:556px}
.hero-photo{position:absolute;inset:0;background:linear-gradient(100deg,#7a1f2a 0%,#a33a45 28%,#cdbfb5 50%,#e9e4dd 70%,#7d8a5a 92%)}
.hero-shade{position:absolute;inset:0;background:rgba(40,20,20,.28)}
.hero-text{position:absolute;left:0;width:1200px;top:208px;text-align:center;color:var(--white)}
.hero-kicker{font-size:26px;font-weight:600}
.hero-title{font-size:40px;font-weight:700;line-height:47px;margin-top:10px}
.hero-sub{font-size:16px;line-height:22px;margin:10px auto 0;width:860px}
.btn{display:flex;align-items:center;justify-content:center;background:var(--purple);color:var(--white);border-radius:30px;font-weight:600;text-decoration:none}
.hero-btn{position:absolute;left:444px;top:415px;width:312px;height:58px;font-size:22px}

/* about */
.about-photo{left:144px;top:840px;width:435px;height:494px;background:linear-gradient(120deg,#2b7fd0 0%,#3c8fe0 40%,#2b2540 70%,#c7d4d8 100%)}
.label{font-size:22px;font-weight:700;letter-spacing:3px;color:var(--teal-text)}
.about-label{left:680px;top:886px}
.about-title{left:680px;top:934px;font-size:34px;line-height:42px;font-weight:600;width:440px}
.about-copy{left:680px;top:1080px;width:420px;font-size:14px;line-height:22px;color:#444}
.about-btn{left:678px;top:1221px;width:192px;height:57px;font-size:22px}

/* services */
.services-band{left:74px;top:1387px;width:1052px;height:408px;background:var(--teal);text-align:center}
.services-band .kicker{margin-top:120px;font-size:18px;letter-spacing:2px;color:var(--white);font-weight:600}
.services-band h2{margin-top:20px;font-size:50px;line-height:61px;font-weight:700;color:var(--purple)}
.card{top:1842px;width:506px;height:461px;color:var(--white);text-align:center;overflow:hidden}
.card-photo{position:absolute;inset:0}
.card.left{left:73px}
.card.left .card-photo{background:linear-gradient(135deg,#b98fc0,#8e5a97 55%,#a57aa9)}
.card.right{left:620px}
.card.right .card-photo{background:linear-gradient(135deg,#d9a9d8,#c68fcc 50%,#cfa3d1)}
.card-body{position:absolute;left:0;width:100%;top:50px}
.card-icon{display:block;margin:0 auto}
.card h3{font-size:36px;font-weight:600;margin-top:12px}
.card p{font-size:16px;line-height:22px;width:340px;margin:16px auto 0}
.card .btn{margin:22px auto 0;height:60px;font-size:22px}

/* testimonials */
.t-label{left:0;width:1200px;top:2398px;text-align:center;font-size:18px;color:var(--teal);letter-spacing:2px;font-weight:600}
.t-title{left:0;width:1200px;top:2424px;text-align:center;font-size:50px;font-weight:700;color:var(--purple)}
.testimonial{top:2536px;width:320px;text-align:center}
.testimonial .quote{font-size:44px;line-height:36px;font-weight:800;color:var(--purple)}
.testimonial h4{font-size:30px;font-weight:400;margin-top:12px}
.testimonial hr{width:122px;margin:10px auto 0;border:0;border-top:1px solid #999}
.testimonial p{font-size:21px;line-height:33px;font-style:italic;color:#444;margin-top:16px}

/* videos */
.v-label{left:0;width:1200px;top:2852px;text-align:center;font-size:18px;letter-spacing:2px;color:var(--teal);font-weight:600}
.v-title{left:0;width:1200px;top:2878px;text-align:center;font-size:50px;font-weight:700;color:var(--purple)}
.video{top:2986px;width:305px}
.video .thumb{height:189px;position:relative}
.video .play{position:absolute;left:50%;top:50%;width:40px;height:40px;margin:-20px 0 0 -20px;border-radius:50%;border:2px solid rgba(255,255,255,.7)}
.video h5{font-size:13px;font-weight:700;margin-top:24px}
.video p{font-size:12px;line-height:23px;color:#444;margin-top:4px}
.load-more{left:0;width:1200px;top:3372px;text-align:center;font-size:15px;text-decoration:underline}

/* footer */
.footer{left:74px;top:3450px;width:1052px;height:355px;background:var(--purple);color:var(--white)}
.footer h3{position:absolute;left:56px;top:66px;font-size:30px;font-weight:600}
.f-loc{position:absolute;left:58px;top:122px;font-size:20px;font-weight:600;display:flex;gap:16px;align-items:center}
.f-addr{position:absolute;left:91px;top:168px;font-size:17px;line-height:33px}
.f-mid{position:absolute;left:349px;top:126px;font-size:17px;line-height:33px}
.f-mid a{text-decoration:underline}
.f-news{position:absolute;left:608px;top:122px;font-size:20px;font-weight:600}
.f-input{position:absolute;left:606px;top:178px;width:307px;height:46px;border-radius:24px;background:var(--white);color:#888;font-size:15px;padding:14px 22px}
.f-join{position:absolute;left:920px;top:178px;width:86px;height:46px;border-radius:24px;background:var(--white);color:var(--purple);font-size:20px;font-weight:700;display:flex;align-items:center;justify-content:center}
.copyright{left:0;width:1200px;top:3838px;text-align:center;font-size:16px;color:#555}
</style>
</head>
<body>

<header class="abs topbar">
  <div class="abs contact-line">555-014-2260 &nbsp;|&nbsp; hello@solvanewellness.com</div>
  <div class="abs brand"><i></i>Solvane Wellness USA</div>
  <div class="abs socials"><span></span><span></span><span></span><span></span></div>
  <div class="abs login"><i></i>Login</div>
</header>
<nav class="abs nav">
  <ul><li class="active">Home</li><li>About us</li><li>Treatment</li><li>FAQ</li><li>Contact us</li></ul>
</nav>

<section class="abs hero">
  <div class="hero-photo" role="img" aria-label="Photo of a woman in a red sweater sitting on a sofa, holding her back in discomfort"></div>
  <div class="hero-shade"></div>
  <div class="hero-text">
    <div class="hero-kicker">Solvane Wellness</div>
    <h1 class="hero-title">We are a new mental health clinic<br>based in Florida called Solvane Wellness USA</h1>
    <p class="hero-sub">Sed ut perspiciatis unde omnis iste natus error sit voluptatem accusantium doloremque laudantium, totam rem aperiam, eaque ipsa quae ab illo inventore veritatis et quasi</p>
  </div>
  <a class="btn hero-btn">Make an Appointment</a>
</section>

<section>
  <div class="abs about-photo" role="img" aria-label="Photo of a nurse in blue scrubs comforting a patient"></div>
  <div class="abs label about-label">ABOUT</div>
  <h2 class="abs about-title">Sed ut perspiciatis unde omnis iste natus error sit voluptatem</h2>
  <p class="abs about-copy">sed quia consequuntur magni dolores eos qui ratione voluptatem sequi nesciunt. Neque porro quisquam est, qui dolorem ipsum quia dolor sit amet, consectetur, adipisci velit, sed quia non numquam eius modi tempora incidunt ut labore et dolore magnam aliquam quaerat voluptatem.</p>
  <a class="abs btn about-btn">Read More</a>
</section>

<section class="abs services-band">
  <div class="kicker">SERVICES</div>
  <h2>Treatment Sessions<br>in Private or in a Group</h2>
</section>

<article class="abs card left">
  <div class="card-photo" role="img" aria-label="Photo of a woman sitting hunched over, feeling low"></div>
  <div class="card-body">
    <svg class="card-icon" width="70" height="86" viewBox="0 0 70 86" fill="none" stroke="#fff" stroke-width="3"><circle cx="35" cy="40" r="13"/><path d="M8 84v-8a27 16 0 0 1 54 0v8z"/><path d="M22 4l-4 10h6l-4 10M50 4l-4 10h6l-4 10"/></svg>
    <h3>Depression</h3>
    <p>Ut enim ad minima veniam, quis nostrum exercitationem ullam corporis suscipit laboriosam, nisi ut aliquid ex ea commodi consequatur</p>
    <a class="btn" style="width:192px">Read More</a>
  </div>
</article>
<article class="abs card right">
  <div class="card-photo" role="img" aria-label="Photo of a man in a clinic holding his shoulder in pain"></div>
  <div class="card-body">
    <svg class="card-icon" width="70" height="86" viewBox="0 0 70 86" fill="none" stroke="#fff" stroke-width="3"><path d="M20 84c0-10 6-14 6-22-6-6-8-14-8-24a18 18 0 0 1 36 0c0 6 4 10 6 14l-6 2v10c0 4-4 6-10 6"/><path d="M44 70c4 4 10 6 14 14"/></svg>
    <h3>Chronic pain</h3>
    <p>Ut enim ad minima veniam, quis nostrum exercitationem ullam corporis suscipit laboriosam, nisi ut aliquid ex ea commodi consequatur</p>
    <a class="btn" style="width:322px">Explore More Services</a>
  </div>
</article>

<div class="abs t-label">TESTIMONIALS</div>
<h2 class="abs t-title">Patients Recommend</h2>
<div class="abs testimonial" style="left:70px"><div class="quote">“</div><h4>Rosa T.</h4><hr><p>“I'm a testimonial. Click to edit me and add text that says something nice about you and your services.”</p></div>
<div class="abs testimonial" style="left:440px"><div class="quote">“</div><h4>Daniel K.</h4><hr><p>“I'm a testimonial. Click to edit me and add text that says something nice about you and your services.”</p></div>
<div class="abs testimonial" style="left:803px"><div class="quote">“</div><h4>Priya N.</h4><hr><p>“I'm a testimonial. Click to edit me and add text that says something nice about you and your services.”</p></div>

<div class="abs v-label">VIDEOS</div>
<h2 class="abs v-title">Development in Motion</h2>
<div class="abs video" style="left:186px">
  <div class="thumb" role="img" aria-label="Video still of a doctor and patient giving a thumbs up beside a spine model" style="background:linear-gradient(120deg,#e8eef2,#b9cde0 50%,#f2f2f2)"></div>
  <h5>Lorem ipsum dolor sit amet, | 00:31</h5>
  <p>Quis autem vel eum iure reprehenderit qui in ea voluptate velit esse quam nihil</p>
</div>
<div class="abs video" style="left:539px">
  <div class="thumb" role="img" aria-label="Video still of a therapist taking notes during a session" style="background:linear-gradient(120deg,#ece8e6,#4a2a3a 45%,#8a4a3a 75%,#e8e0da)"><span class="play"></span></div>
  <h5>Lorem ipsum dolor sit amet, | 00:31</h5>
  <p>Quis autem vel eum iure reprehenderit qui in ea voluptate velit esse quam nihil</p>
</div>
<div class="abs video" style="left:891px">
  <div class="thumb" role="img" aria-label="Video still of a man at a desk rubbing his sore neck" style="background:linear-gradient(120deg,#f0f2f4,#c8d4e4 50%,#eef0f2)"><span class="play"></span></div>
  <h5>Lorem ipsum dolor sit amet, | 00:31</h5>
  <p>Quis autem vel eum iure reprehenderit qui in ea voluptate velit esse quam nihil</p>
</div>
<div class="abs load-more">Load More</div>

<footer class="abs footer">
  <h3>Contact Me</h3>
  <div class="f-loc"><svg width="16" height="22" viewBox="0 0 16 22"><path d="M8 0a8 8 0 0 0-8 8c0 6 8 14 8 14s8-8 8-14a8 8 0 0 0-8-8z" fill="#fff"/><circle cx="8" cy="8" r="3" fill="#8e2d8a"/></svg>Solvane</div>
  <div class="f-addr">218 Palmetto Lane<br>Orlando, FL 32801</div>
  <div class="f-mid">Tel 555-014-2260<br>Email hello@solvanewellness.com<br><a>Book a Consultation</a><br><a>Join a Workshop</a></div>
  <div class="f-news">Subscribe to Get My Newsletter</div>
  <div class="f-input">Enter Your Email</div>
  <div class="f-join">Join</div>
</footer>
<div class="abs copyright">© 2019 | www.solvanewellness.com</div>

</body>
</html>
```